Coastline Premier Retreats Business Card Design

Design a business card for Coastline Premier Retreats. Look at the website for colors and reference. Card should have logo, name, title, office number, mobile number, email, URL and a tagline like, "Luxury Hotel & Resort Email Marketing" (This might change).

https://www.coastlinepremierretreats.example

The rest I will leave up to your imagination.

Contact Information for Business Card

Logo, name, title, office number, mobile number, email, URL and a tagline like, "Luxury Hotel & Resort Email Marketing" (This might change).

```html
<!DOCTYPE html>
<html lang="en">
<head>
<meta charset="utf-8">
<title>Coastline Premier Retreats – Business Card</title>
<link rel="stylesheet" href="https://fonts.googleapis.com/css2?family=Arimo:wght@400;700&display=swap">
<style>
  :root {
    --stage: #2a2a2a;
    --card: #1e1e1e;
    --orange: #f07a12;
    --white: #ffffff;
    --text-soft: #e6e6e6;
    --emboss: #2b2b2b;
    --emboss-edge: #353535;
  }
  * { box-sizing: border-box; margin: 0; padding: 0; }
  html, body {
    width: 1200px; height: 915px; overflow: hidden;
    background: var(--stage);
    font-family: "Arimo", Arial, sans-serif;
  }
  .stage {
    position: relative; width: 1200px; height: 915px;
    display: flex; align-items: center; justify-content: center; gap: 50px;
  }
  .card {
    position: relative; width: 540px; height: 309px;
    background: var(--card); border-radius: 16px; overflow: hidden;
    box-shadow: 0 18px 40px rgba(0,0,0,.45);
  }

  /* Back side */
  .card--back .brand-mark {
    position: absolute; left: 0; right: 0; top: 112px;
    display: flex; align-items: center; justify-content: center; gap: 14px;
  }
  .card--back .brand-square {
    width: 26px; height: 26px; background: var(--emboss-edge);
  }
  .card--back .brand-name {
    font-weight: 700; font-size: 34px; letter-spacing: 1px;
    color: var(--emboss); text-transform: uppercase;
    text-shadow: none;
  }
  .card--back .brand-name { color: #3a3a3a; }
  .tagline {
    position: absolute; left: 0; right: 0; top: 205px;
    text-align: center; color: var(--orange); font-size: 15px;
  }

  /* Front side */
  .card--front .brand-mark {
    position: absolute; right: 34px; top: 40px;
    display: flex; align-items: center; gap: 10px;
  }
  .card--front .brand-square {
    width: 16px; height: 16px; background: var(--orange);
  }
  .card--front .brand-name {
    font-weight: 700; font-size: 17px; color: var(--white);
    text-transform: uppercase; letter-spacing: .5px;
  }
  .divider-top {
    position: absolute; left: 230px; right: 34px; top: 92px;
    height: 1px; background: var(--orange);
  }
  .person { position: absolute; left: 34px; top: 128px; }
  .person__name {
    font-weight: 700; font-size: 26px; color: var(--orange);
    text-transform: uppercase; letter-spacing: .5px;
  }
  .person__title { font-size: 15px; color: var(--text-soft); margin-top: 2px; }
  .divider-person {
    position: absolute; left: 34px; width: 230px; top: 192px;
    height: 1px; background: var(--orange);
  }
  .contacts {
    position: absolute; left: 34px; top: 204px; list-style: none;
    font-size: 13.5px; color: var(--white); line-height: 19px;
  }
  .contacts li { display: flex; align-items: center; gap: 9px; }
  .contacts svg { width: 11px; height: 11px; fill: var(--orange); flex: none; }
  .address {
    position: absolute; right: 34px; top: 200px; text-align: right;
    font-size: 13.5px; color: var(--white); line-height: 19px;
  }
  .footer-band {
    position: absolute; left: 0; right: 0; bottom: 0; height: 12px; display: flex;
  }
  .footer-band__accent { width: 66%; background: var(--orange); }
  .footer-band__light { flex: 1; background: var(--white); }
</style>
</head>
<body>
<main class="stage">
  <section class="card card--back" aria-label="Card back">
    <div class="brand-mark">
      <span class="brand-square"></span>
      <span class="brand-name">Coastline Premier Retreats</span>
    </div>
    <p class="tagline">Luxury Hotel &amp; Resort Email Marketing</p>
  </section>

  <section class="card card--front" aria-label="Card front">
    <div class="brand-mark">
      <span class="brand-square"></span>
      <span class="brand-name">Coastline Premier Retreats</span>
    </div>
    <div class="divider-top"></div>

    <div class="person">
      <h1 class="person__name">Marcus Delaney</h1>
      <p class="person__title">CEO/Founder</p>
    </div>
    <div class="divider-person"></div>

    <ul class="contacts">
      <li><svg viewBox="0 0 12 12"><path d="M3 0h6a1 1 0 0 1 1 1v10a1 1 0 0 1-1 1H3a1 1 0 0 1-1-1V1a1 1 0 0 1 1-1zm0 1.5v8h6v-8z"/></svg>555.214.7300</li>
      <li><svg viewBox="0 0 12 12"><path d="M1 4c0-2 2-3 5-3s5 1 5 3l-2 1-1-1.5H4L3 5zM3 6h6l1 5H2z"/></svg>+34 600 482 917</li>
      <li><svg viewBox="0 0 12 12"><path d="M0 2h12v8H0zm1 1v.4l5 3.2 5-3.2V3z"/></svg>info@coastlinepremierretreats.example</li>
      <li><svg viewBox="0 0 12 12"><circle cx="6" cy="6" r="6"/></svg>www.coastlinepremierretreats.example</li>
    </ul>

    <address class="address" style="font-style:normal">
      Po Box, 48 Harbor Lane<br>Bayview, CA 90000
    </address>

    <div class="footer-band">
      <span class="footer-band__accent"></span>
      <span class="footer-band__light"></span>
    </div>
  </section>
</main>
</body>
</html>
```